Tech Company New PowerPoint Design Project

We are an IT Managed services, cloud and cyber security company https://www.travolin.com.au/ Requesting proposals for a PowerPoint deck template that can be used by our sales team when pitching clients, our head office is located in Australa and we do have regional offices in NZ , USA , SRI LANKA and SINGAPORE. and also required to have a proposal/SOW template created too (not sure if this is something that we can include to this proposal) we may need a lot of things done in future but this is where i like to get started for now.. please let m eknow your thoughts and if you have any questions.
Target Market(s)
Enterprise
Industry/Entity Type
Information Technology
Look and feel

```html
<!DOCTYPE html>
<html lang="en">
<head>
<meta charset="utf-8">
<title>Travolin – Sales Deck</title>
<link rel="stylesheet" href="https://fonts.googleapis.com/css2?family=Montserrat:wght@300;400;500;600;700&family=Nunito:wght@300;700;800&display=swap">
<style>
:root{
  --page:#1f1f1f;
  --cyan:#29c4f4;
  --cyan-deep:#17a9e6;
  --navy:#0f2f57;
  --navy-2:#1c5a8a;
  --ice:#e7f4fb;
  --ink:#1a1a1a;
  --body:#444;
  --white:#fff;
  --icon:#3aa9dc;
}
*{box-sizing:border-box;margin:0;padding:0}
html,body{width:1200px;height:3914px;overflow:hidden;background:var(--page)}
body{position:relative;font-family:"Montserrat",sans-serif;color:var(--ink)}
.slide{position:absolute;left:102px;width:1001px;height:564px;overflow:hidden}
.abs{position:absolute}
.wordmark{font-family:"Nunito",sans-serif;font-weight:300;color:var(--cyan);letter-spacing:2px;line-height:1}

/* cover */
.cover{top:112px;background:linear-gradient(135deg,#0d2c55 0%,#1a4f80 45%,#2a7fb0 75%,#134a78 100%)}
.cover .wordmark{left:0;right:0;top:58px;text-align:center;font-size:112px}
.rule{position:absolute;height:3px;background:var(--cyan)}
.cover h1{position:absolute;left:0;right:0;top:258px;text-align:center;font-family:"Nunito",sans-serif;font-weight:800;font-size:56px;color:var(--white)}
.cover h1 span{color:var(--cyan)}
.cover p{position:absolute;left:190px;right:190px;top:400px;text-align:center;font-size:16.5px;line-height:25px;color:var(--white)}

/* about */
.about{top:734px;background:var(--ice)}
.about .photo{position:absolute;left:512px;top:0;width:489px;height:564px;background:linear-gradient(160deg,#0a2240 0%,#16467a 50%,#0b1d36 100%)}
.about .wordmark{left:26px;top:14px;font-size:56px}
.about h2{position:absolute;left:37px;top:112px;font-size:26px;font-weight:700}
.about .lead{position:absolute;left:37px;top:163px;width:420px;font-size:12.8px;line-height:19px;color:var(--body)}
.bullet{position:absolute;left:37px;width:430px;padding-left:31px;font-size:12.8px;line-height:19px;color:var(--body)}
.bullet::before{content:"";position:absolute;left:0;top:5px;width:14px;height:14px;border-radius:50%;background:var(--cyan-deep)}

/* service desk */
.desk{top:1355px;background:var(--ice)}
.desk .wordmark{left:26px;top:16px;font-size:56px}
.pill{position:absolute;background:var(--cyan);color:var(--white);font-weight:700;border-radius:12px;text-align:center}
.desk .pill{left:271px;top:22px;width:377px;height:48px;line-height:48px;font-size:25px}
.desk .banner{position:absolute;left:0;top:91px;width:1001px;height:281px;background:linear-gradient(180deg,#0a1f4d 0%,#1146a0 60%,#3a86d6 100%)}
.card{position:absolute;background:var(--white);border-radius:12px;text-align:center}
.card svg{display:block;margin:0 auto}
.card h3{font-size:14px;font-weight:700;line-height:20px;color:var(--ink)}
.card p{font-size:12.8px;line-height:19px;color:var(--body)}
.desk .card{top:234px;width:225px;height:304px;padding:26px 18px 0}
.desk .card h3{margin-top:18px}
.desk .card p{margin-top:14px}

/* services */
.services{top:1976px;background:var(--ice)}
.services .wordmark{left:26px;top:14px;font-size:56px}
.services h2{position:absolute;left:68px;top:150px;font-size:30px;font-weight:700}
.services .card{width:225px;height:240px;padding:22px 14px 0}
.services .card h3{margin-top:14px;font-size:13.5px}
.services .card p{margin-top:8px;font-size:11.5px;line-height:15.6px}

/* partners */
.partners{top:2597px;background:var(--ice)}
.partners .wordmark{left:82px;top:22px;font-size:50px}
.partners .pill{left:707px;top:28px;width:210px;height:38px;line-height:38px;font-size:22px}
.grid{position:absolute;left:84px;top:87px;width:836px;display:grid;grid-template-columns:repeat(4,209px);grid-auto-rows:64px;border-left:1px solid #d5e3ec}
.cell{border-right:1px solid #d5e3ec;display:flex;align-items:center;justify-content:center}
.row-alt{background:#dcecf6}
.badge{height:20px;border-radius:3px;background:#9aa8b3}

/* closing */
.closing{top:3219px;background:linear-gradient(180deg,#2ccaf6 0%,#19b3ee 60%,#12a6e6 100%)}
.closing .wordmark{left:0;right:0;top:56px;text-align:center;font-size:110px;color:var(--white)}
.closing .rule{background:var(--white)}
.closing h1{position:absolute;left:0;right:0;top:210px;text-align:center;font-family:"Nunito",sans-serif;font-weight:300;font-size:80px;color:var(--white)}
.office{position:absolute;top:403px;color:var(--white);font-size:12.3px;line-height:16px;text-transform:uppercase}
.office h4{font-size:15px;font-weight:700;margin-bottom:8px}
.divider{position:absolute;top:405px;width:1px;height:132px;background:rgba(255,255,255,.8)}
</style>
</head>
<body>

<!-- Cover -->
<section class="slide cover">
  <div class="abs" role="img" aria-label="Blue network constellation background" style="inset:0"></div>
  <div class="abs wordmark">travolin</div>
  <div class="rule" style="left:210px;width:580px;top:248px"></div>
  <h1>Welcome to <span>TRAVOLIN</span></h1>
  <div class="rule" style="left:210px;width:580px;top:343px"></div>
  <p>TRAVOLIN is a one-stop destination for all your IT Management Requirements. We are committed to delivering cutting-edge, simplified IT solutions through our highly skilled team and flexible engagement models.</p>
</section>

<!-- About -->
<section class="slide about">
  <div class="abs wordmark">travolin</div>
  <h2>ABOUT US</h2>
  <p class="lead">TRAVOLIN is a one-stop destination for all your IT Management Requirements. We are committed to delivering cutting-edge, simplified IT solutions through our highly skilled team and flexible engagement models. Whether you need support for integration or ongoing operational services, TRAVOLIN has the insight and technical capability to deliver simplified solutions.</p>
  <p class="bullet" style="top:310px">Our passion, enthusiasm, and value are what make us different from our peers. While there are many businesses providing the same services, what we deliver is unparalleled. Whether services or solutions, we keep standing with our clients through thick and thin.</p>
  <p class="bullet" style="top:436px">Whether you need support for integration or ongoing operational services, TRAVOLIN has the insight and technical capability to deliver simplified solutions.</p>
  <div class="photo" role="img" aria-label="Photo of hands typing on a laptop showing code with floating data screens"></div>
</section>

<!-- Managed service desk -->
<section class="slide desk">
  <div class="abs wordmark">travolin</div>
  <div class="pill">MANAGED SERVICE DESK</div>
  <div class="banner" role="img" aria-label="Blue digital network wave background"></div>
  <div class="card" style="left:28px">
    <svg width="64" height="64" viewBox="0 0 64 64" fill="none" stroke="var(--icon)" stroke-width="2"><rect x="6" y="6" width="52" height="14" rx="2"/><rect x="6" y="25" width="52" height="14" rx="2"/><rect x="6" y="44" width="52" height="14" rx="2"/><circle cx="48" cy="13" r="1.5"/><circle cx="48" cy="32" r="1.5"/><circle cx="48" cy="51" r="1.5"/><path d="M12 13h20M12 32h20M12 51h20"/></svg>
    <h3>Server &amp;<br>Network Support</h3>
    <p>Address issues and bugs of your server and network devices as a remote service</p>
  </div>
  <div class="card" style="left:268px">
    <svg width="64" height="64" viewBox="0 0 64 64" fill="none" stroke="var(--icon)" stroke-width="2"><circle cx="32" cy="14" r="7"/><path d="M20 38c0-8 6-13 12-13s12 5 12 13z"/><path d="M8 20v22l12 14M56 20v22L44 56"/></svg>
    <h3>Desktop &amp;<br>End User Support</h3>
    <p>Address technical issues and bugs of your desktop environment as well as your users as a remote service</p>
  </div>
  <div class="card" style="left:508px">
    <svg width="64" height="64" viewBox="0 0 64 64" fill="none" stroke="var(--icon)" stroke-width="2"><path d="M16 24a10 10 0 0 1 4-14 14 14 0 0 1 26 2 9 9 0 0 1 4 12z"/><rect x="14" y="28" width="36" height="9" rx="2"/><rect x="14" y="40" width="36" height="9" rx="2"/><rect x="14" y="52" width="36" height="9" rx="2"/></svg>
    <h3>Managed Backup &amp;<br>Recovery</h3>
    <p>Provide a data backup and restore service to protect your information and documents against internal accidents, threats. Including recovery management</p>
  </div>
  <div class="card" style="left:748px">
    <svg width="64" height="64" viewBox="0 0 64 64" fill="none" stroke="var(--icon)" stroke-width="2"><rect x="6" y="20" width="52" height="36" rx="2"/><path d="M12 48l10-10 8 6 10-14 12 8"/><circle cx="32" cy="10" r="5"/><path d="M32 15v5"/></svg>
    <h3>Network<br>Monitoring</h3>
    <p>Monitor each device that connected to network in 24 x 7 and maintain the high level of availability of services</p>
  </div>
</section>

<!-- Services -->
<section class="slide services">
  <div class="abs wordmark">travolin</div>
  <h2>SERVICES</h2>
  <div class="card" style="left:287px;top:36px">
    <svg width="52" height="52" viewBox="0 0 52 52" fill="none" stroke="var(--icon)" stroke-width="2"><rect x="6" y="28" width="40" height="18" rx="2"/><circle cx="26" cy="16" r="7"/><circle cx="42" cy="8" r="5"/><path d="M12 36h28"/></svg>
    <h3>Service Desk</h3>
    <p>Single point of contact for incident and service request handling &amp; remote support including a fixed monthly rate with unlimited support under service level agreements through global coverage</p>
  </div>
  <div class="card" style="left:524px;top:36px">
    <svg width="52" height="52" viewBox="0 0 52 52" fill="none" stroke="var(--icon)" stroke-width="2"><rect x="8" y="8" width="36" height="36" rx="3"/><circle cx="26" cy="26" r="7"/><path d="M26 4v8M26 40v8M4 26h8M40 26h8"/></svg>
    <h3>Network<br>Operations Center</h3>
    <p>Monitor each device that connected to network in 24 x 7 and maintain the high level of availability of services</p>
  </div>
  <div class="card" style="left:762px;top:36px">
    <svg width="52" height="52" viewBox="0 0 52 52" fill="none" stroke="var(--icon)" stroke-width="2"><rect x="6" y="10" width="40" height="28" rx="2"/><path d="M18 46h16M26 38v8M12 18h14M12 24h20M12 30h10"/></svg>
    <h3>Procurement Services</h3>
    <p>The procurement team is specialized in sourcing and supplying products and license to meet our customer’s needs.</p>
  </div>
  <div class="card" style="left:45px;top:290px">
    <svg width="52" height="52" viewBox="0 0 52 52" fill="none" stroke="var(--icon)" stroke-width="2"><path d="M14 46V36a16 16 0 1 1 22-4v14"/><circle cx="27" cy="20" r="6"/><path d="M27 10v4M27 26v4M17 20h4M33 20h4"/></svg>
    <h3>AI as a Service</h3>
    <p>Artificial Intelligence (AI) can reduce the number of hours your business spends on managing your IT operations.</p>
  </div>
  <div class="card" style="left:287px;top:290px">
    <svg width="52" height="52" viewBox="0 0 52 52" fill="none" stroke="var(--icon)" stroke-width="2"><rect x="26" y="6" width="20" height="16" rx="2"/><circle cx="18" cy="24" r="6"/><path d="M8 46c0-9 5-14 10-14s10 5 10 14M30 32h16v14H28"/></svg>
    <h3>Software Development</h3>
    <p>Design unique software as per your business requirement,provide reliable total hosting service by using managed host platforms</p>
  </div>
  <div class="card" style="left:524px;top:290px">
    <svg width="52" height="52" viewBox="0 0 52 52" fill="none" stroke="var(--icon)" stroke-width="2"><rect x="10" y="6" width="28" height="38" rx="2"/><path d="M16 16h16M16 22h16M16 28h10"/><circle cx="38" cy="38" r="7"/></svg>
    <h3>Project Services</h3>
    <p>Provide secured and high-quality service for ad hoc or multi-site project works with on time deliverables</p>
  </div>
  <div class="card" style="left:762px;top:290px">
    <svg width="52" height="52" viewBox="0 0 52 52" fill="none" stroke="var(--icon)" stroke-width="2"><path d="M24 4l18 7v13c0 12-8 19-18 23C14 43 6 36 6 24V11z"/><path d="M16 24l6 6 10-12"/><rect x="32" y="34" width="12" height="10" rx="1"/></svg>
    <h3>Security Operations Center</h3>
    <p>The TRAVOLIN SOC Team provides large-scale Cyber Security Coverage for organizations to protect their Confidentially, Integrity, and Availability (CIA). We are offering Vulnerability Assessments.</p>
  </div>
</section>

<!-- Partners -->
<section class="slide partners">
  <div class="abs wordmark">travolin</div>
  <div class="pill">OUR PARTNERS</div>
  <div class="grid">
    <div class="cell"><div class="badge" style="width:76px"></div></div><div class="cell"><div class="badge" style="width:110px"></div></div><div class="cell"><div class="badge" style="width:46px"></div></div><div class="cell"><div class="badge" style="width:50px"></div></div>
    <div class="cell row-alt"><div class="badge" style="width:140px;height:26px"></div></div><div class="cell row-alt"><div class="badge" style="width:80px;height:12px"></div></div><div class="cell row-alt"><div class="badge" style="width:60px;height:12px"></div></div><div class="cell row-alt"><div class="badge" style="width:86px"></div></div>
    <div class="cell"><div class="badge" style="width:66px"></div></div><div class="cell"><div class="badge" style="width:40px;height:26px"></div></div><div class="cell"><div class="badge" style="width:130px;height:30px"></div></div><div class="cell"><div class="badge" style="width:92px;height:26px"></div></div>
    <div class="cell row-alt"><div class="badge" style="width:58px"></div></div><div class="cell row-alt"><div class="badge" style="width:62px;height:26px"></div></div><div class="cell row-alt"><div class="badge" style="width:104px;height:26px"></div></div><div class="cell row-alt"><div class="badge" style="width:64px"></div></div>
    <div class="cell"><div class="badge" style="width:54px"></div></div><div class="cell"><div class="badge" style="width:76px"></div></div><div class="cell"><div class="badge" style="width:40px;height:10px"></div></div><div class="cell"><div class="badge" style="width:86px;height:26px"></div></div>
    <div class="cell row-alt"><div class="badge" style="width:58px"></div></div><div class="cell row-alt"><div class="badge" style="width:52px;height:14px"></div></div><div class="cell row-alt"><div class="badge" style="width:68px;height:24px"></div></div><div class="cell row-alt"><div class="badge" style="width:60px;height:12px"></div></div>
    <div class="cell"><div class="badge" style="width:92px"></div></div><div class="cell"><div class="badge" style="width:30px;height:24px"></div></div><div class="cell"><div class="badge" style="width:66px;height:24px"></div></div><div class="cell"></div>
  </div>
</section>

<!-- Closing -->
<section class="slide closing">
  <div class="abs" role="img" aria-label="Light cyan network constellation background" style="inset:0"></div>
  <div class="abs wordmark">travolin</div>
  <div class="rule" style="left:308px;width:388px;top:198px"></div>
  <h1>Thank You</h1>
  <div class="rule" style="left:308px;width:388px;top:318px"></div>

  <div class="office" style="left:37px;width:180px">
    <h4>Australia</h4>
    TRAVOLIN PTY LIMITED<br><span style="text-transform:none">www.travolin.com.au</span><br>ABN 41 503 118 274<br>PO BOX 214 RIVERTON<br>2077 NSW<br>AUSTRALIA
  </div>
  <div class="divider" style="left:214px"></div>
  <div class="office" style="left:262px;width:290px">
    <h4>Sri Lanka</h4>
    TRAVOLIN ASIA PACIFIC ( PRIVATE) LIMITED<br>(PV 00487302)<br>14/6, HARBOUR VIEW BUILDING 3RD FLOOR<br>LOTUS GROVE ROAD<br>00700, COLOMBO<br>SRI LANKA
  </div>
  <div class="divider" style="left:550px"></div>
  <div class="office" style="left:594px;width:200px">
    <h4>New Zealand</h4>
    TRAVOLIN NZ PTY LIMITED<br>NZBN 948 215 6630 917<br>22/40 KOWHAI STREET<br><span style="text-transform:none">Riverlea</span><br><span style="text-transform:none">Hamilton NZ 3204</span><br>NEW ZEALAND
  </div>
  <div class="divider" style="left:786px"></div>
  <div class="office" style="left:824px;width:175px">
    <h4>Singapore</h4>
    TRAVOLIN NZ PTY LIMITED<br>NZBN 948 215 6630 917<br>22/40 KOWHAI STREET<br><span style="text-transform:none">Riverlea</span><br><span style="text-transform:none">Singapore&nbsp; 3204</span><br>SINGAPORE
  </div>
</section>

</body>
</html>
```